Business Card for Coastal Tundrabridge Advisory

We need a business card for Coastal Tundrabridge Advisory. The company website address is provided below. The company logo is attached. We provide specialized permafrost services to the mining, transportation, and oil & gas industries. The card should be prepared for:
Matthias Korhonen, PhD.
Coastal Tundrabridge Advisory
PO Box 418259
Quillwater, Alaska 99642
Direct: +1-907-555-0143
Email: mkorhonen@tundrabridgeadvisory.example
Website: www.coastaltundrabridgeadvisory.example

```html
<!DOCTYPE html>
<html lang="en">
<head>
<meta charset="utf-8">
<title>Coastal Tundrabridge Advisory — Business Card</title>
<link rel="stylesheet" href="https://fonts.googleapis.com/css2?family=Montserrat:wght@400;500;600;700&display=swap">
<style>
  :root {
    --backdrop: #8a7358;
    --card-front: #ffffff;
    --card-back: #111820;
    --ink: #151a20;
    --ink-soft: #2a2f36;
    --paper-text: #f4f5f6;
    --rule: #1c2127;
  }
  * { box-sizing: border-box; margin: 0; padding: 0; }
  html, body {
    width: 900px; height: 1200px; overflow: hidden;
    background: var(--backdrop);
    font-family: "Montserrat", sans-serif;
  }
  .canvas { position: relative; width: 900px; height: 1200px; }

  .card {
    position: absolute;
    border-radius: 22px;
    box-shadow: 0 12px 28px rgba(0,0,0,0.35);
  }
  .card--front { left: 80px; top: 131px; width: 742px; height: 440px; background: var(--card-front); color: var(--ink); }
  .card--back { left: 78px; top: 640px; width: 744px; height: 438px; background: var(--card-back); color: var(--paper-text); }

  .brand-name {
    position: absolute;
    text-transform: uppercase;
    text-align: center;
    font-weight: 600;
    line-height: 1.25;
  }
  .card--front .brand-name {
    left: 40px; top: 218px; width: 276px;
    font-size: 15px; letter-spacing: 2px; color: var(--ink);
  }
  .card--back .brand-name {
    left: 0; top: 190px; width: 100%;
    font-size: 30px; letter-spacing: 5px; color: var(--paper-text);
  }

  .divider { position: absolute; left: 316px; top: 161px; width: 2px; height: 143px; background: var(--rule); }

  .person { position: absolute; left: 328px; top: 158px; }
  .person__name { font-size: 22px; font-weight: 700; letter-spacing: 0.1px; color: var(--ink); }
  .person__title { font-size: 15px; font-weight: 500; margin-top: 3px; color: var(--ink-soft); }

  .contact-list { position: absolute; left: 330px; top: 220px; list-style: none; }
  .contact-list__item { display: flex; align-items: center; height: 30.5px; font-size: 15px; font-weight: 500; color: var(--ink); }
  .contact-list__icon { width: 16px; height: 16px; margin-right: 13px; flex: none; }

  .address { position: absolute; left: 0; top: 384px; width: 708px; text-align: center; font-size: 15px; font-weight: 500; color: var(--ink); }
</style>
</head>
<body>
<div class="canvas">

  <section class="card card--front" aria-label="Business card front">
    <div class="brand-name">Coastal<br>Tundrabridge Advisory</div>
    <div class="divider"></div>
    <div class="person">
      <div class="person__name">Matthias Korhonen, PhD.</div>
      <div class="person__title">Managing Director</div>
    </div>
    <ul class="contact-list">
      <li class="contact-list__item">
        <svg class="contact-list__icon" viewBox="0 0 24 24" aria-hidden="true">
          <path fill="var(--ink)" d="M6.6 10.8a15.1 15.1 0 0 0 6.6 6.6l2.2-2.2a1 1 0 0 1 1-.25 11.4 11.4 0 0 0 3.6.57 1 1 0 0 1 1 1V20a1 1 0 0 1-1 1A17 17 0 0 1 3 4a1 1 0 0 1 1-1h3.5a1 1 0 0 1 1 1c0 1.25.2 2.45.57 3.57a1 1 0 0 1-.25 1z"/>
          <path fill="none" stroke="var(--ink)" stroke-width="1.8" d="M14 3.5a7 7 0 0 1 6.5 6.5M14 7a3.5 3.5 0 0 1 3 3"/>
        </svg>
        +1-907-555-0143
      </li>
      <li class="contact-list__item">
        <svg class="contact-list__icon" viewBox="0 0 24 24" aria-hidden="true">
          <rect x="4" y="6" width="16" height="12" rx="1.5" fill="var(--ink)"/>
          <path d="M4.5 7l7.5 6 7.5-6" fill="none" stroke="#fff" stroke-width="1.5"/>
        </svg>
        mkorhonen@tundrabridgeadvisory.example
      </li>
      <li class="contact-list__item">
        <svg class="contact-list__icon" viewBox="0 0 24 24" aria-hidden="true">
          <circle cx="12" cy="12" r="9" fill="var(--ink)"/>
          <path d="M3 12h18M12 3c3 3 3 15 0 18M12 3c-3 3-3 15 0 18" fill="none" stroke="#fff" stroke-width="1.3"/>
        </svg>
        www.coastaltundrabridgeadvisory.example
      </li>
    </ul>
    <div class="address">PO Box 418259 Quillwater, Alaska 99642</div>
  </section>

  <section class="card card--back" aria-label="Business card back">
    <div class="brand-name">Coastal<br>Tundrabridge Advisory</div>
  </section>

</div>
</body>
</html>
```